Brightmill Data Works

Our company is about IT hardwares and IT solutions. IT hardware such as PC, RAMS, storage and servers. IT solutions such as project management, BA. We are also selling new technology too.

Target Market(s)

Consumer, Small to Medium Business, Corporate

Requirements
Must have
• The business card must have the following:
• Name:
• Title:
• Contact Number:
• Email address:
• Website:
• Color: Must match the logo color upgrade

```html
<!DOCTYPE html>
<html lang="en">
<head>
<meta charset="UTF-8">
<title>Brightmill Data Works – Business Card</title>
<link rel="stylesheet" href="https://fonts.googleapis.com/css2?family=Arimo:wght@400;700&display=swap">
<style>
  :root {
    --page: #dcdcdc;
    --card-white: #ffffff;
    --charcoal: #4a4849;
    --ink: #454445;
    --copper: #d0892e;
    --light-text: #ffffff;
  }
  * { box-sizing: border-box; margin: 0; padding: 0; }
  html, body { width: 1200px; height: 880px; overflow: hidden; }
  body {
    background: var(--page);
    font-family: "Arimo", Arial, sans-serif;
    position: relative;
  }
  .card {
    position: absolute;
    width: 600px;
    height: 343px;
    border-radius: 22px;
    overflow: hidden;
    background: var(--card-white);
    box-shadow: 0 10px 28px rgba(0,0,0,0.22);
  }
  .card-front { left: 100px; top: 70px; }
  .card-back  { left: 500px; top: 467px; }

  .wordmark {
    display: flex;
    align-items: center;
    gap: 12px;
  }
  .wordmark-square {
    width: 22px; height: 22px;
    background: var(--copper);
    flex: none;
  }
  .wordmark-name {
    font-weight: 700;
    color: var(--ink);
    text-transform: uppercase;
    line-height: 1.05;
    letter-spacing: 0.5px;
  }

  .card-front .wordmark {
    position: absolute;
    left: 0; right: 0; top: 118px;
    justify-content: center;
  }
  .card-front .wordmark-name { font-size: 34px; }
  .front-url {
    position: absolute;
    left: 0; right: 0; top: 228px;
    text-align: center;
    font-size: 13px;
    font-weight: 700;
    letter-spacing: 3px;
    color: var(--ink);
  }

  .back-shapes { position: absolute; inset: 0; }
  .card-back .wordmark {
    position: absolute;
    left: 375px; top: 118px;
  }
  .card-back .wordmark-name { font-size: 25px; }

  .person { position: absolute; left: 48px; top: 62px; color: var(--light-text); }
  .person-name { font-size: 19px; font-weight: 700; text-transform: uppercase; }
  .person-title { font-size: 15px; margin-top: 2px; }

  .address {
    position: absolute; left: 48px; top: 170px;
    color: var(--light-text); font-size: 15px; line-height: 1.3;
  }
  .contacts {
    position: absolute; left: 48px; top: 226px;
    list-style: none; color: var(--light-text); font-size: 15px;
  }
  .contacts li { display: flex; align-items: center; gap: 10px; height: 22px; }
  .contacts svg { width: 13px; height: 13px; flex: none; }
</style>
</head>
<body>

  <section class="card card-front" aria-label="Business card front">
    <div class="wordmark">
      <span class="wordmark-square"></span>
      <span class="wordmark-name">Brightmill Data Works</span>
    </div>
    <p class="front-url">www.BRIGHTMILLDATA.com</p>
  </section>

  <section class="card card-back" aria-label="Business card back">
    <svg class="back-shapes" viewBox="0 0 600 343" width="600" height="343" aria-hidden="true">
      <path d="M0 0 H330 C365 140 430 265 555 343 H0 Z" fill="var(--charcoal)"/>
      <path d="M343 0 C378 140 445 262 575 343" fill="none" stroke="var(--copper)" stroke-width="3"/>
      <circle cx="0" cy="118" r="15" fill="var(--page)"/>
    </svg>

    <div class="person">
      <p class="person-name">Dana Whitfield</p>
      <p class="person-title">Manager</p>
    </div>

    <p class="address">PO Box 482 Harbor Lane<br>7th Street Ashford</p>

    <ul class="contacts">
      <li>
        <svg viewBox="0 0 16 16" aria-hidden="true"><path fill="#fff" d="M3 1h3l1.5 4-2 1.3a9 9 0 0 0 4.2 4.2L11 8.5l4 1.5v3a2 2 0 0 1-2 2A12 12 0 0 1 1 3a2 2 0 0 1 2-2z"/></svg>
        555-204-7731
      </li>
      <li>
        <svg viewBox="0 0 16 16" aria-hidden="true"><rect x="1" y="3" width="14" height="10" fill="#fff"/><path d="M1 3l7 6 7-6" fill="none" stroke="var(--charcoal)" stroke-width="1.4"/></svg>
        info@brightmilldata.com
      </li>
      <li>
        <svg viewBox="0 0 16 16" aria-hidden="true"><g fill="none" stroke="#fff" stroke-width="1.3"><circle cx="8" cy="8" r="6.5"/><ellipse cx="8" cy="8" rx="3" ry="6.5"/><path d="M1.5 8h13"/></g></svg>
        www.brightmilldata.com
      </li>
    </ul>

    <div class="wordmark">
      <span class="wordmark-square"></span>
      <span class="wordmark-name">Brightmill<br>Data Works</span>
    </div>
  </section>

</body>
</html>
```